Kelvor Engineers: Why you should hire us keepsake

New design. Open to plastic cards. We are an engineering firm that designs cell phone towers and commercial buildings. Please check out our website www.kelvorstruct.com for more details. We want people to remember our card and for it to be useful if possible. We want the same look and feel on these cards to be translated to other marketing material we may need such as brochures.

Target Market(s)

Architects, Developers and Telecommunication Carriers

Industry/Entity Type

Engineering

Contact Information for Business Card

Card with our company colors, logo, and innovative design with elements related to our industry.

Font styles to use
Sans Serif

Colors
9bcb3c
abd036
0255a3

Requirements
Must have
• Sleek and hip design
Nice to have
• Bright lime green and navy coloring that pops with an innovative design.
Should not have
• A basic and boring design

```html
<!DOCTYPE html>
<html lang="en">
<head>
<meta charset="UTF-8">
<title>Kelvor Engineers – Business Card</title>
<link href="https://fonts.googleapis.com/css2?family=Roboto:wght@400;500;700;900&display=swap" rel="stylesheet">
<style>
  :root {
    --navy: #1b3566;
    --navy-deep: #15295a;
    --lime: #cdd92a;
    --white: #ffffff;
    --backdrop: #2b2b2b;
    --ink: #1f3a78;
  }
  * { box-sizing: border-box; margin: 0; padding: 0; }
  html, body {
    width: 1200px; height: 930px; overflow: hidden;
    background: var(--backdrop);
    font-family: "Roboto", sans-serif;
  }
  .stage { position: relative; width: 1200px; height: 930px; }

  .card {
    position: absolute;
    width: 560px; height: 320px;
    border-radius: 18px;
    overflow: hidden;
  }

  /* Front */
  .card-front {
    left: 70px; top: 110px;
    background: var(--navy);
  }
  .card-front .wordmark {
    position: absolute; left: 0; right: 0; top: 108px;
    text-align: center;
    font-weight: 900; font-size: 52px; letter-spacing: -0.5px;
    color: var(--lime);
  }
  .card-front .tagline {
    position: absolute; left: 0; right: 0; top: 186px;
    text-align: center;
    font-weight: 500; font-size: 14px; letter-spacing: 1.6px;
    color: var(--white);
  }

  /* Back */
  .card-back {
    left: 570px; top: 500px;
    background: var(--white);
  }
  .card-back .sweep { position: absolute; inset: 0; }
  .card-back .wordmark {
    position: absolute; left: 34px; top: 44px;
    font-weight: 900; font-size: 34px; letter-spacing: -0.3px;
    color: var(--lime);
  }
  .contact-block { position: absolute; left: 40px; top: 140px; }
  .person-name { font-weight: 500; font-size: 21px; color: var(--ink); }
  .person-role { font-size: 14px; color: var(--lime); margin-top: 2px; }
  .rule { width: 96px; height: 1.5px; background: var(--ink); margin: 8px 0 10px; }
  .contact-list { list-style: none; }
  .contact-list li {
    display: flex; align-items: center; gap: 10px;
    font-size: 14px; color: var(--ink); line-height: 21px;
  }
  .contact-list svg { width: 11px; height: 11px; flex: none; }
  .cities {
    position: absolute; right: 30px; top: 104px;
    text-align: right;
    font-weight: 500; font-size: 17px; line-height: 22px; letter-spacing: 0.6px;
    color: var(--white);
  }
</style>
</head>
<body>
<main class="stage">

  <section class="card card-front" aria-label="Business card front">
    <div class="wordmark">Kelvor Engineers</div>
    <div class="tagline">MULTI-DISCIPLINE ENGINEERING</div>
  </section>

  <section class="card card-back" aria-label="Business card back">
    <svg class="sweep" viewBox="0 0 560 320" preserveAspectRatio="none" aria-hidden="true">
      <path d="M392 0 C372 170 290 288 0 300 L0 320 L560 320 L560 0 Z" fill="var(--lime)"/>
      <path d="M404 0 C386 178 302 300 0 312 L0 320 L560 320 L560 0 Z" fill="var(--white)"/>
      <path d="M410 0 C392 182 308 306 0 316 L0 320 L560 320 L560 0 Z" fill="var(--navy)"/>
    </svg>

    <div class="wordmark">Kelvor Engineers</div>

    <div class="contact-block">
      <div class="person-name">Dana Whitlow</div>
      <div class="person-role">Director</div>
      <div class="rule"></div>
      <ul class="contact-list">
        <li>
          <svg viewBox="0 0 12 12"><path d="M2.5 1 L4.5 1 L5.2 3.6 L3.9 4.6 C4.6 6 6 7.4 7.4 8.1 L8.4 6.8 L11 7.5 L11 9.5 C11 10.3 10.3 11 9.5 11 C5 11 1 7 1 2.5 C1 1.7 1.7 1 2.5 1 Z" fill="var(--lime)"/></svg>
          555.210.4830
        </li>
        <li>
          <svg viewBox="0 0 12 12"><rect x="3" y="0.8" width="6" height="10.4" rx="1.2" fill="none" stroke="var(--lime)" stroke-width="1.4"/></svg>
          555.384.1962
        </li>
        <li>
          <svg viewBox="0 0 12 12"><rect x="0.8" y="2.2" width="10.4" height="7.6" rx="1" fill="none" stroke="var(--lime)" stroke-width="1.3"/><path d="M1 3 L6 6.8 L11 3" fill="none" stroke="var(--lime)" stroke-width="1.3"/></svg>
          dwhitlow@kelvorstruct.com
        </li>
        <li>
          <svg viewBox="0 0 12 12"><circle cx="6" cy="6" r="5.2" fill="var(--lime)"/></svg>
          www.kelvorstruct.com
        </li>
      </ul>
    </div>

    <div class="cities">ATLANTA<br>CHARLOTTE<br>HOUSTON<br>SAN ANTONIO</div>
  </section>

</main>
</body>
</html>
```